Förderverein einer Kirchengemeinde sucht Flyer-Design
Zielgruppe
Wir sind ein Förderverein einer Kirchengemeinde, der sich für die kirchenmusikalische Arbeit einsetzt.
Wir wünschen uns ein niveauvolles und zeitgemäßes/modernes Flyerdesign, das die etablierten Konzertbesucher anspricht, aber vor allem auch Menschen erreicht und überzeugt, die (noch) nichts mit Kirche zu tun haben.
Das Alter der (Haupt-) Zielgruppe (Männer und Frauen) erstreckt sich von 45 bis 70 Jahren.
Aufgabenstellung
Bei der Wahl des Formates würden wir (aus der Sicht von Laien) ein zweimal gefaltetes DIN A4 quer Format nehmen. Aber wir lassen uns gerne überraschen und sind grundsätzlich für andere Lösungen offen.
Bitte den Abschnitt für Adress- und sonstige Dateneintragungen samt Kontodaten so gestalten und platzieren, dass man ihn leicht abtrennen und verschicken kann.
Der Flyer soll Kirchenmusik als lebendig und attraktiv darstellen und neue (jüngere) Mitglieder für den Freundeskreis werben.
Lassen Sie die Bilder sprechen!!

```html
<!DOCTYPE html>
<html lang="de">
<head>
<meta charset="utf-8">
<title>Freundeskreis Kirchenmusik – Innenseiten</title>
<link href="https://fonts.googleapis.com/css2?family=Mulish:wght@300;400;600;700&display=swap" rel="stylesheet">
<style>
  :root{
    --bg:#d9d9db;
    --paper:#f7f7f7;
    --paper-shade:#e4e4e5;
    --brand-red:#b3191e;
    --panel-red:#b5171c;
    --text:#4a4a4a;
    --text-strong:#2e2e2e;
    --white:#ffffff;
  }
  *{margin:0;padding:0;box-sizing:border-box}
  html,body{width:1200px;height:661px;overflow:hidden;background:var(--bg)}
  body{font-family:"Mulish",sans-serif;color:var(--text);position:relative}
  .spread{position:absolute;left:20px;top:122px;width:1160px;height:416px;
    box-shadow:0 10px 24px rgba(0,0,0,.18)}
  .spread-art{position:absolute;inset:0}
  .text{position:absolute;line-height:1.42}
  .intro-title{left:0;width:336px;top:44px;text-align:right;color:var(--brand-red);
    font-weight:600;font-size:17px;line-height:1.15}
  .intro-rule{position:absolute;left:344px;top:43px;width:1px;height:90px;background:var(--brand-red)}
  .intro-copy{left:354px;top:49px;width:190px;font-size:9.6px;font-weight:300}
  .intro-copy p+p{margin-top:8px}
  .benefit-title{left:232px;top:160px;color:var(--brand-red);font-weight:600;font-size:12px}
  .benefit-item{font-size:9.2px;font-weight:300;width:300px;text-indent:0}
  .benefit-item b{font-weight:700;color:var(--text-strong)}
  .reasons-title{left:870px;top:48px;color:var(--white);font-weight:700;font-size:13.5px}
  .reasons-lead{left:879px;top:83px;color:var(--white);font-size:10px;font-weight:400}
  .reason-item{color:var(--white);font-size:9.4px;font-weight:400;width:220px}
</style>
</head>
<body>
<main class="spread" aria-label="Innenseiten des Flyers Freundeskreis Kirchenmusik">
  <svg class="spread-art" width="1160" height="416" viewBox="0 0 1160 416" aria-hidden="false">
    <defs>
      <linearGradient id="paperLeft" x1="0" x2="1" y1="0" y2="0">
        <stop offset="0" stop-color="#fbfbfb"/><stop offset=".85" stop-color="#efefef"/><stop offset="1" stop-color="#dcdcdd"/>
      </linearGradient>
      <linearGradient id="brass" x1="0" y1="0" x2="1" y2="1">
        <stop offset="0" stop-color="#8a7440"/><stop offset=".5" stop-color="#c9a95a"/><stop offset="1" stop-color="#5b5248"/>
      </linearGradient>
      <linearGradient id="garden" x1="0" y1="0" x2="0" y2="1">
        <stop offset="0" stop-color="#3f5a2c"/><stop offset=".6" stop-color="#8a8f84"/><stop offset="1" stop-color="#6f6b4e"/>
      </linearGradient>
      <linearGradient id="kids" x1="0" y1="0" x2="0" y2="1">
        <stop offset="0" stop-color="#2f4a26"/><stop offset=".55" stop-color="#d7b83a"/><stop offset="1" stop-color="#6b6a55"/>
      </linearGradient>
      <linearGradient id="brassChoir" x1="0" y1="0" x2="0" y2="1">
        <stop offset="0" stop-color="#d2d0c8"/><stop offset=".6" stop-color="#bdb8ab"/><stop offset="1" stop-color="#7d7a72"/>
      </linearGradient>
      <linearGradient id="concert" x1="0" y1="0" x2="0" y2="1">
        <stop offset="0" stop-color="#b9a48d"/><stop offset=".45" stop-color="#4a3c37"/><stop offset="1" stop-color="#1c1a1b"/>
      </linearGradient>
      <linearGradient id="panel" x1="0" y1="0" x2="1" y2="1">
        <stop offset="0" stop-color="#a8161b"/><stop offset="1" stop-color="#c01b20"/>
      </linearGradient>
    </defs>

    <rect class="page-left" x="0" y="0" width="583" height="416" fill="url(#paperLeft)"/>
    <rect class="page-right" x="583" y="0" width="577" height="416" fill="var(--paper)"/>

    <polygon role="img" aria-label="Foto: Hände an einer Trompete aus Messing" points="0,0 164,0 190,120 0,120" fill="url(#brass)"/>
    <polygon role="img" aria-label="Foto: Flötenensemble mit Blockflöten im Garten" points="0,121 190,121 223,271 0,271" fill="url(#garden)"/>
    <polygon role="img" aria-label="Foto: Kinderchor in gelben T-Shirts vor einer Hecke" points="0,272 223,272 254,416 0,416" fill="url(#kids)"/>

    <polygon role="img" aria-label="Foto: Posaunenchor mit Blechblasinstrumenten auf einer Treppe" points="583,0 836,0 884,204 583,204" fill="url(#brassChoir)"/>
    <polygon role="img" aria-label="Foto: Kantorei beim Konzert im Kirchenraum mit Dirigent" points="583,205 884,205 921,416 583,416" fill="url(#concert)"/>
    <polygon points="836,0 842,0 929,416 921,416" fill="#8c8d92" opacity=".55"/>

    <polygon class="reasons-panel" points="842,0 1160,0 1160,416 929,416" fill="url(#panel)"/>

    <rect x="575" y="0" width="16" height="416" fill="#000" opacity=".06"/>
  </svg>

  <h1 class="text intro-title">Kirchenmusik<br>braucht Freunde</h1>
  <div class="intro-rule"></div>
  <div class="text intro-copy">
    <p>Im Jahr 1999 gegründet, unterstützt der Freundeskreis Kirchenmusik die vielfältigen musikalischen Aktivitäten an der St. Alberti-Kirche.</p>
    <p>Wir laden Sie ein, Mitglied zu werden!</p>
  </div>

  <h2 class="text benefit-title">Mit Ihrem Beitrag …</h2>
  <p class="text benefit-item" style="left:236px;top:190px">…bereichern Sie Lindenhagens kulturelle Landschaft durch den Erhalt<br>&nbsp;&nbsp;&nbsp;&nbsp;und Ausbau unseres hohen kirchenmusikalischen Niveaus</p>
  <p class="text benefit-item" style="left:244px;top:226px">… stärken Sie das Ehrenamt</p>
  <p class="text benefit-item" style="left:250px;top:248px">… ermöglichen Sie der <b>Kantorei</b>, dem <b>Posaunenchor</b>, dem<br>&nbsp;&nbsp;&nbsp;&nbsp;<b>Kinderchor</b> und dem <b>Flötenensemble</b> regelmäßige Proben-<br>&nbsp;&nbsp;&nbsp;&nbsp;arbeit, Probenwochenenden und die Anschaffung von<br>&nbsp;&nbsp;&nbsp;&nbsp;&nbsp;Notenmaterial</p>
  <p class="text benefit-item" style="left:263px;top:307px;width:320px">…erhalten Sie die historische <b>Matthias Kellner Orgel von 1748</b></p>
  <p class="text benefit-item" style="left:267px;top:329px">…fördern Sie die Ausbildung kirchenmusikalischen Nach-<br>&nbsp;&nbsp;&nbsp;&nbsp;&nbsp;wuchses</p>

  <h2 class="text reasons-title">Mitglieder haben gute Gründe:</h2>
  <p class="text reasons-lead">Sie…</p>
  <p class="text reason-item" style="left:884px;top:108px">… erhalten ermäßigte Eintrittspreise von<br>&nbsp;&nbsp;&nbsp;&nbsp;gemeindeeigenen Konzerten</p>
  <p class="text reason-item" style="left:896px;top:150px">… können Konzertkarten vor dem öffentlichen<br>&nbsp;&nbsp;&nbsp;&nbsp;Verkauf erwerben</p>
  <p class="text reason-item" style="left:905px;top:192px">… gestalten die Arbeit des Freundeskreises<br>&nbsp;&nbsp;&nbsp;&nbsp;&nbsp;in den jährlichen Mitgliederversammlungen<br>&nbsp;&nbsp;&nbsp;&nbsp;&nbsp;aktiv mit</p>
  <p class="text reason-item" style="left:920px;top:250px">… erhalten aktuelle Informationen über<br>&nbsp;&nbsp;&nbsp;&nbsp;Veranstaltungen der Gemeinde bequem<br>&nbsp;&nbsp;&nbsp;&nbsp;&nbsp;per Email und profitieren so zu allererst</p>
  <p class="text reason-item" style="left:933px;top:307px">… können den Mitgliedsbeitrag steuerlich<br>&nbsp;&nbsp;&nbsp;&nbsp;absetzen und erhalten eine Spenden-<br>&nbsp;&nbsp;&nbsp;&nbsp;&nbsp;bescheinigung</p>
</main>
</body>
</html>
```